Military and tactical gear supply company needs web design

We need a web design for a company called U.S. Torvane. We provide quality tactical equipment to military and law enforcement. This is an e-commerce business and we primarily market ourselves on social media. Our key products are backpacks, military-style belts, and tactical flashlights. The gear we sell is not yet widely known about, but is on par with the state-of-the-art products in this field. We want the website to convey the message of quality, durability, and reliability. We use the word "kinetic" because the customers in this field are very "action-oriented" and we would like that idea to be communicated in the web site as well. The primary demographic is men in their 20's-30's, so the web site should have a masculine feel to it. Attached is the logo and color scheme.

```html
<!DOCTYPE html>
<html lang="en">
<head>
<meta charset="utf-8">
<title>U.S. Torvane – Tactical Gear</title>
<link href="https://fonts.googleapis.com/css2?family=Montserrat:wght@400;500;600;700&family=Roboto:wght@400;500&display=swap" rel="stylesheet">
<style>
:root{
  --red:#a30a1e;
  --navy:#234f6b;
  --ink:#1d1d1d;
  --text:#4a4a4a;
  --light:#f2f2f2;
  --footer:#1e1e1e;
  --star:#f5a623;
}
*{margin:0;padding:0;box-sizing:border-box}
html,body{width:1200px;height:3553px;overflow:hidden;background:#fff}
body{position:relative;font-family:'Roboto',sans-serif;color:var(--ink)}
.abs{position:absolute}
.btn{position:absolute;display:flex;align-items:center;justify-content:center;background:var(--navy);color:#fff;font-family:'Montserrat',sans-serif;font-size:19px;font-weight:500;text-transform:uppercase}
.heading{font-family:'Montserrat',sans-serif;font-weight:500;text-transform:uppercase}

/* header */
.topbar{top:0;left:0;width:1200px;height:112px}
.contact{left:88px;top:38px;display:flex;gap:10px;align-items:center}
.contact small{display:block;font-family:'Montserrat',sans-serif;font-size:17px;font-weight:500}
.contact strong{display:block;font-family:'Montserrat',sans-serif;font-size:20px;font-weight:500}
.brand{left:0;width:1200px;top:30px;text-align:center;font-family:'Montserrat',sans-serif;font-weight:700;font-size:36px;color:var(--navy);letter-spacing:1px}
.brand span{display:block;font-size:14px;font-weight:600;letter-spacing:0}
.social{right:90px;top:46px;display:flex;gap:12px}
.social i{display:block;width:26px;height:26px;background:var(--navy);border-radius:3px}
.nav{top:112px;left:0;width:1200px;height:61px;background:var(--light)}
.nav ul{position:absolute;left:92px;top:0;height:61px;display:flex;gap:44px;align-items:center;list-style:none;font-family:'Montserrat',sans-serif;font-size:18px;font-weight:500}
.nav li.active{color:var(--red);text-decoration:underline;text-underline-offset:6px}
.quote{left:878px;top:112px;width:232px;height:61px}

/* hero */
.hero{top:173px;left:0;width:1200px;height:583px;background:radial-gradient(ellipse at 50% 45%,#5b5530 0%,#3e3a22 45%,#1f1d14 100%)}
.hero h1{position:absolute;top:165px;width:1200px;text-align:center;font-family:'Montserrat',sans-serif;font-weight:700;font-size:60px;color:#fff}
.hero p{position:absolute;top:243px;left:230px;width:740px;text-align:center;color:#fff;font-size:17px;line-height:32px}
.hero .btn{left:503px;top:320px;width:193px;height:56px}

/* about */
.about-title{left:88px;top:846px;font-size:38px;color:var(--red)}
.about-copy{left:88px;top:902px;width:460px;font-size:16.5px;line-height:32.2px;color:var(--text);text-align:justify}
.about .btn{left:88px;top:1186px;width:214px;height:59px}
.about-photo{left:686px;top:854px;width:424px;height:389px;background:linear-gradient(135deg,#4a4a4a,#1e1e1e 60%,#2e3328)}

/* features */
.features{top:1341px;left:0;width:1200px;height:257px;background:var(--light)}
.features .lead{position:absolute;left:0;top:0;width:395px;height:257px;background:var(--red);color:#fff;padding:46px 30px 0 86px}
.lead h3{font-family:'Montserrat',sans-serif;font-weight:500;font-size:26px;margin-bottom:12px}
.lead p{font-size:16px;line-height:29px;text-align:justify}
.feature{position:absolute;top:34px;height:196px;text-align:center}
.feature h4{font-family:'Montserrat',sans-serif;font-weight:500;font-size:20px;margin:12px 0 10px}
.feature p{font-size:14px;line-height:23px;color:var(--text)}
.divider{position:absolute;top:36px;width:1px;height:196px;background:#cfcfcf}

/* products */
.products-title{left:0;width:1200px;top:1688px;text-align:center;font-size:40px;color:var(--red)}
.card{position:absolute;top:1773px;width:325px;height:392px;background:var(--light);text-align:center}
.card .photo{position:absolute;left:4px;top:4px;width:317px;height:199px;background:#fff;display:flex;align-items:center;justify-content:center;overflow:hidden}
.card .photo div{border-radius:8px}
.card h5{position:absolute;left:0;top:218px;width:325px;font-family:'Montserrat',sans-serif;font-weight:500;font-size:22px;line-height:28px;color:var(--red)}
.card p{position:absolute;left:16px;top:261px;width:293px;font-size:15px;line-height:27px;color:var(--text);text-align:justify;text-align-last:center}
.card .btn{left:78px;top:366px;width:170px;height:50px;font-size:17px}

/* reviews */
.reviews{top:2288px;left:0;width:1200px;height:472px;background:radial-gradient(ellipse at center,#2f2a24,#151311)}
.reviews h2{position:absolute;top:38px;width:1200px;text-align:center;color:#fff;font-size:38px}
.bubble{position:absolute;top:117px;width:469px;height:170px;background:var(--light);border-radius:6px;padding:22px 3px;font-size:16px;line-height:28px;color:var(--text);text-align:justify}
.tail{position:absolute;top:286px}
.person{position:absolute;top:327px;display:flex;gap:12px;color:#fff}
.avatar{width:68px;height:68px;border-radius:50%;background:#6b5a4b;border:3px solid #d8d8d8}
.person b{display:block;font-family:'Montserrat',sans-serif;font-weight:500;font-size:21px}
.person small{display:block;font-family:'Montserrat',sans-serif;font-size:15px;margin:2px 0}
.person em{font-style:normal;color:var(--star);font-size:19px;letter-spacing:3px}
.dots{position:absolute;top:431px;left:572px;display:flex;gap:8px}
.dots i{width:12px;height:12px;border-radius:50%;background:#fff}
.dots i.on{background:var(--red)}

/* cta */
.cta-title{left:0;width:1200px;top:2848px;text-align:center;font-size:36px;color:var(--red)}
.cta-copy{left:220px;width:760px;top:2910px;text-align:center;font-size:20px;line-height:34px}
.cta .btn{left:453px;top:2996px;width:296px;height:58px}

/* footer */
.footer{top:3136px;left:0;width:1200px;height:417px;background:var(--footer);color:#fff}
.col{position:absolute;top:72px}
.col h6{font-family:'Montserrat',sans-serif;font-weight:500;font-size:20px;margin-bottom:22px}
.col ul{list-style:none;font-size:15.5px;line-height:34px}
.field{position:absolute;left:882px;width:225px;height:43px;border:1px solid #ddd;font-size:12px;padding:15px 8px}
.submit{left:992px;top:301px;width:115px;height:36px;font-size:15px}
.copyright{position:absolute;top:366px;width:1200px;text-align:center;font-family:'Montserrat',sans-serif;font-size:18px}
</style>
</head>
<body>

<header class="abs topbar">
  <div class="abs contact">
    <svg width="34" height="34" viewBox="0 0 34 34"><circle cx="17" cy="17" r="15.5" fill="none" stroke="#234f6b" stroke-width="2"/><path d="M11 10c1-1 2-1 3 0l2 3c.5 1 0 2-1 2.5 1 2 2.5 3.5 4.5 4.5.5-1 1.5-1.5 2.5-1l3 2c1 1 1 2 0 3-2 2-5 1.5-8-1.5S9 12 11 10z" fill="#234f6b"/></svg>
    <div><small>CONTACT US:</small><strong>555.210.4478</strong></div>
  </div>
  <div class="abs brand">U.S. TORVANE<span>ustorvane.com</span></div>
  <div class="abs social" aria-label="Social links"><i></i><i></i><i></i></div>
</header>

<nav class="abs nav">
  <ul><li class="active">HOME</li><li>ABOUT US</li><li>PRODUCTS</li><li>BLOG</li><li>CONTACT US</li></ul>
</nav>
<div class="btn quote">GET A QUOTE</div>

<section class="abs hero" role="img" aria-label="Tactical vest, rifle, gloves and boots laid out in warm low light">
  <h1>U.S. TORVANE</h1>
  <p>Lorem ipsum dolor sit amet, consectetur adipiscing elit, sed do eiusmod tempor incididunt ut labore et dolore magna aliqua. Ut enim ad minim veniam, quis nostrud exercitation ullamco</p>
  <div class="btn">GET STARTED</div>
</section>

<section class="about">
  <h2 class="abs heading about-title">About Us</h2>
  <p class="abs about-copy">Lorem ipsum dolor sit amet, consectetur adipiscing elit, sed do eiusmod tempor incididunt ut labore et dolore magna aliqua. Ut enim ad minim veniam, quis nostrud exercitation ullamco laboris nisi ut aliquip ex ea commodo consequat. Duis aute irure dolor in reprehenderit in voluptate velit esse cillum dolore eu fugiat nulla pariatur. Excepteur sint occaecat cupidatat non proident, sunt in culpa qui officia deserunt mollit anim id est laborum</p>
  <div class="btn">READ MORE</div>
  <div class="abs about-photo" role="img" aria-label="Tactical gear, grenades, flashlight and handcuffs on dark wood"></div>
</section>

<section class="abs features">
  <div class="lead">
    <h3>FINIBUS BONORUM</h3>
    <p>Lorem ipsum dolor sit amet, consectetur adipiscing elit, sed do eiusmod tempor incididunt ut labore et dolore magna aliqua.</p>
  </div>
  <div class="feature" style="left:420px;width:205px">
    <svg width="70" height="70" viewBox="0 0 70 70" fill="none" stroke="#234f6b" stroke-width="2.2"><rect x="12" y="8" width="40" height="56" rx="3"/><rect x="24" y="4" width="16" height="8" rx="2"/><path d="M18 24l4 4 6-7M18 38l4 4 6-7M18 52l4 4 6-7M34 26h12M34 40h8"/><path d="M62 18L44 48l-4 6 6-4 18-30z"/></svg>
    <h4>QUALITY</h4>
    <p>Lorem ipsum dolor sit amet,<br>consectetur adipiscing elit</p>
  </div>
  <div class="divider" style="left:632px"></div>
  <div class="feature" style="left:645px;width:205px">
    <svg width="70" height="70" viewBox="0 0 70 70" fill="none" stroke="#234f6b" stroke-width="2.2"><circle cx="35" cy="35" r="32"/><circle cx="35" cy="35" r="8"/><path d="M18 18l34 34M35 20v5M35 45v5M20 35h5M45 35h5"/></svg>
    <h4>DURABILITY</h4>
    <p>Lorem ipsum dolor sit amet,<br>consectetur adipiscing elit</p>
  </div>
  <div class="divider" style="left:865px"></div>
  <div class="feature" style="left:890px;width:215px;top:30px">
    <svg width="76" height="86" viewBox="0 0 76 86" fill="none" stroke="#234f6b" stroke-width="2.4"><path d="M38 3L72 14v26c0 22-16 36-34 43C20 76 4 62 4 40V14z"/><path d="M38 12L63 20v20c0 16-11 27-25 33C24 67 13 56 13 40V20z"/><circle cx="38" cy="42" r="14"/><path d="M31 42l5 5 9-10"/></svg>
    <h4>RELIABILITY</h4>
    <p>Lorem ipsum dolor sit amet,<br>consectetur adipiscing elit</p>
  </div>
</section>

<h2 class="abs heading products-title">Products</h2>
<article class="card" style="left:88px">
  <div class="photo"><div role="img" aria-label="Brown tactical backpack" style="background:#8a6a45;width:150px;height:175px"></div></div>
  <h5>BACKPACKS</h5>
  <p>Lorem ipsum dolor sit amet, consectetur adipiscing elit, sed do eiusmod tempor incididunt ut labore et dolore magna aliqua.</p>
  <div class="btn">VIEW MORE</div>
</article>
<article class="card" style="left:437px">
  <div class="photo"><div role="img" aria-label="Camouflage military-style belt" style="background:#2f4a2e;width:260px;height:110px"></div></div>
  <h5>MILITARY-STYLE BELTS</h5>
  <p>Lorem ipsum dolor sit amet, consectetur adipiscing elit, sed do eiusmod tempor incididunt ut labore et dolore magna aliqua.</p>
  <div class="btn">VIEW MORE</div>
</article>
<article class="card" style="left:785px">
  <div class="photo"><div role="img" aria-label="Black tactical flashlight" style="background:#262626;width:240px;height:100px"></div></div>
  <h5>TACTICAL FLASHLIGHTS</h5>
  <p>Lorem ipsum dolor sit amet, consectetur adipiscing elit, sed do eiusmod tempor incididunt ut labore et dolore magna aliqua.</p>
  <div class="btn">VIEW MORE</div>
</article>

<section class="abs reviews">
  <h2 class="heading">Reviews</h2>
  <div class="bubble" style="left:118px">Lorem ipsum dolor sit amet, consectetur adipiscing elit, sed do eiusmod tempor incididunt ut labore et dolore magna aliqua. Ut enim ad minim veniam, quis nostrud exercitation ullamco laboris nisi ut aliquip ex ea commodo consequat.</div>
  <svg class="tail" style="left:330px" width="100" height="30"><path d="M0 30L100 0H55z" fill="#f2f2f2"/></svg>
  <div class="bubble" style="left:610px">Lorem ipsum dolor sit amet, consectetur adipiscing elit, sed do eiusmod tempor incididunt ut labore et dolore magna aliqua. Ut enim ad minim veniam, quis nostrud exercitation ullamco laboris nisi ut aliquip ex ea commodo consequat.</div>
  <svg class="tail" style="left:822px" width="100" height="30"><path d="M0 30L100 0H55z" fill="#f2f2f2"/></svg>
  <div class="person" style="left:135px">
    <div class="avatar" role="img" aria-label="Reviewer portrait"></div>
    <div><b>MARCO DELVAN</b><small>HARLOW OUTFITTERS, BROOKFIELD</small><em>★★★★★</em></div>
  </div>
  <div class="person" style="left:627px">
    <div class="avatar" role="img" aria-label="Reviewer portrait"></div>
    <div><b>DANA WHITLOCK REYES</b><small>MANAGER, RIDGEWAY TRAINING HALL</small><em>★★★★★</em></div>
  </div>
  <div class="dots"><i></i><i class="on"></i><i></i></div>
</section>

<section class="cta">
  <h2 class="abs heading cta-title">Get Started Today!</h2>
  <p class="abs cta-copy">Lorem ipsum dolor sit amet, consectetur adipiscing elit, sed do eiusmod tempor incididunt ut labore et dolore magna aliqua. Ut enim ad</p>
  <div class="btn">CALL US (555) 000-0000</div>
</section>

<footer class="abs footer">
  <div class="col" style="left:88px"><h6>QUICKS LINKS</h6><ul><li>Home</li><li>About Us</li><li>Product</li><li>Blog</li><li>Contact Us</li></ul></div>
  <div class="col" style="left:324px;top:74px"><h6>PRODUCTS</h6><ul><li>Backpacks</li><li>Military-style belts</li><li>Tactical flashlights</li></ul></div>
  <div class="col" style="left:586px;top:74px"><h6>CONTACT US</h6><ul><li>12 Alder Lane, Fairmont,</li><li>ST, 0000</li><li>555 000 0000</li><li>info@ustorvane.com</li></ul></div>
  <div class="col" style="left:888px"><h6>MESSAGE US</h6></div>
  <div class="field" style="top:131px">NAME</div>
  <div class="field" style="top:180px">EMAIL</div>
  <div class="field" style="top:233px">MESSAGE</div>
  <div class="btn submit">SUBMIT</div>
  <p class="copyright">© Copyright 2020&nbsp; U.S. Torvane.All Rights Reserved</p>
</footer>

</body>
</html>
```